Design marketing/advertisement email for consulting business

Hello - My company, Brantor-Quisse, is looking for a marketing professional to compose a "marketing" email to be sent to potential professional referral sources. The email should provide an introduction of our company's capabilities and services. We want this marketing piece to invite the recipient to schedule a call with us to further discuss how we could best work together. The email must included elements of our brand. Our website is www.brantorquisse.example and will provide you with all the details about our business as well as our logo, branding, contact details etc. Thanks so much!
Updates
Industry/Entity Type
Business

```html
<!DOCTYPE html>
<html lang="en">
<head>
<meta charset="utf-8">
<title>Brantor-Quisse – Services Flyer</title>
<link rel="stylesheet" href="https://fonts.googleapis.com/css2?family=Open+Sans:ital,wght@0,400;0,600;0,700;1,600;1,700&display=swap">
<style>
  :root {
    --paper: #ffffff;
    --ink: #2b2b2b;
    --ink-soft: #3a3a3a;
    --grey-text: #5a5a5a;
    --charcoal: #2a2627;
    --brand-orange: #ee6a40;
    --brand-peach: #f6b58a;
    --room-dark: #3b3431;
    --room-light: #d9d4cf;
    --desk-light: #e9e3dc;
    --panel-veil: rgba(236, 232, 228, 0.78);
  }
  * { box-sizing: border-box; margin: 0; padding: 0; }
  html, body {
    width: 1200px; height: 847px; overflow: hidden;
    background: var(--paper);
    font-family: "Open Sans", Arial, sans-serif;
    color: var(--ink);
  }
  .flyer { position: relative; width: 1200px; height: 847px; overflow: hidden; background: var(--paper); }
  .abs { position: absolute; }

  /* Brand header */
  .brand-header { left: 0; top: 0; width: 462px; height: 200px; background: var(--paper); }
  .brand-mark { left: 49px; top: 62px; width: 60px; height: 60px; background: var(--brand-orange); }
  .brand-name {
    left: 124px; top: 66px; font-size: 38px; font-weight: 400;
    color: var(--ink-soft); letter-spacing: 0.5px; line-height: 52px;
  }

  /* Image areas */
  .photo-desk {
    left: 462px; top: 0; width: 565px; height: 214px;
    background: linear-gradient(135deg, #d8cfc6 0%, var(--desk-light) 45%, #f4f1ed 70%, #cfc5bb 100%);
  }
  .photo-room-left {
    left: 0; top: 200px; width: 462px; height: 647px;
    background: linear-gradient(180deg, #4a423e 0%, var(--room-dark) 40%, #5b534d 70%, #2f2a27 100%);
  }
  .photo-room-right {
    left: 462px; top: 214px; width: 738px; height: 633px;
    background: linear-gradient(90deg, #cfc9c4 0%, var(--room-light) 50%, #c8bfb5 80%, #a79c90 100%);
  }
  .accent-block-top { left: 1027px; top: 0; width: 173px; height: 214px; background: var(--charcoal); }
  .content-veil { left: 462px; top: 214px; width: 504px; height: 633px; background: var(--panel-veil); }
  .footer-bar { left: 690px; top: 810px; width: 510px; height: 37px; background: var(--charcoal); }

  /* Service arrows */
  .service-arrow { left: 0; width: 470px; }
  .service-arrow svg { display: block; }
  .service-title, .service-sub { position: absolute; white-space: nowrap; }
  .service-title { font-weight: 600; color: #fff; }
  .service-sub { font-weight: 400; color: #fff; }
  .arrow-dev { top: 200px; height: 166px; }
  .arrow-dev .service-title { left: 34px; top: 52px; font-size: 29px; }
  .arrow-dev .service-sub { left: 38px; top: 99px; font-size: 19px; }
  .arrow-ops { top: 390px; height: 167px; }
  .arrow-ops .service-title { left: 40px; top: 50px; font-size: 34px; }
  .arrow-ops .service-sub { left: 40px; top: 100px; font-size: 23px; }
  .arrow-exit { top: 591px; height: 168px; }
  .arrow-exit .service-title { left: 40px; top: 50px; font-size: 34px; }
  .arrow-exit .service-sub { left: 40px; top: 100px; font-size: 23px; }

  .site-url { left: 38px; top: 799px; font-size: 17px; color: #fff; }

  /* Service descriptions */
  .service-copy { left: 476px; font-size: 13px; line-height: 15.6px; color: var(--ink-soft); }
  .service-copy h3 { font-size: 13px; font-weight: 700; line-height: 15.6px; color: var(--ink); }
  .copy-feasibility { top: 250px; width: 330px; }
  .copy-audits { top: 402px; width: 334px; }
  .copy-communications { top: 610px; width: 232px; }

  /* Contact */
  .contact-heading { left: 690px; top: 750px; font-size: 32px; font-weight: 400; color: var(--grey-text); }
  .contact-details {
    left: 898px; top: 728px; list-style: none;
    font-size: 17px; line-height: 24.5px; font-weight: 700; font-style: italic; color: var(--grey-text);
  }
</style>
</head>
<body>
<main class="flyer">
  <div class="abs photo-desk" role="img" aria-label="Photo: hands reviewing house elevation drawings on a desk"></div>
  <div class="abs accent-block-top"></div>
  <div class="abs photo-room-right" role="img" aria-label="Photo: bright modern living room with sofa and decorative branch"></div>
  <div class="abs photo-room-left" role="img" aria-label="Photo: dim modern living room interior"></div>
  <div class="abs content-veil"></div>

  <header class="abs brand-header">
    <div class="abs brand-mark"></div>
    <div class="abs brand-name">Brantor-Quisse</div>
  </header>

  <section class="abs service-arrow arrow-dev">
    <svg width="470" height="166" viewBox="0 0 470 166">
      <defs>
        <linearGradient id="gradDev" x1="0" y1="0" x2="0" y2="1">
          <stop offset="0" stop-color="#5a5657"/>
          <stop offset="1" stop-color="#1e1b1c"/>
        </linearGradient>
      </defs>
      <polygon points="0,40 384,40 462,103 384,166 0,166" fill="url(#gradDev)" stroke="#8a8586" stroke-width="1.5"/>
    </svg>
    <h2 class="service-title">DEVELOPMENT SERVICES</h2>
    <p class="service-sub">Acquisition, Planning and Design</p>
  </section>

  <section class="abs service-arrow arrow-ops">
    <svg width="470" height="167" viewBox="0 0 470 167">
      <defs>
        <linearGradient id="gradOps" x1="0" y1="0" x2="1" y2="0">
          <stop offset="0" stop-color="#f4a677"/>
          <stop offset="1" stop-color="#f9d3b6"/>
        </linearGradient>
      </defs>
      <polygon points="0,0 384,0 462,83 384,167 0,167" fill="url(#gradOps)"/>
    </svg>
    <h2 class="service-title">OPERATION</h2>
    <p class="service-sub">Audits and Assessments</p>
  </section>

  <section class="abs service-arrow arrow-exit">
    <svg width="470" height="168" viewBox="0 0 470 168">
      <defs>
        <linearGradient id="gradExit" x1="0" y1="0" x2="1" y2="0">
          <stop offset="0" stop-color="#ec5f35"/>
          <stop offset="1" stop-color="#f59a72"/>
        </linearGradient>
      </defs>
      <polygon points="0,0 384,0 462,84 384,168 0,168" fill="url(#gradExit)"/>
    </svg>
    <h2 class="service-title">DISPOSITION</h2>
    <p class="service-sub">Transition and Exit Strategies</p>
  </section>

  <p class="abs site-url">www.brantorquisse.example</p>

  <article class="abs service-copy copy-feasibility">
    <h3>Feasibility Studies</h3>
    <p>Site selection studies, demographic reports and mystery shopping of the local competition are services offered to ensure that you are building your community in the best location possible to maximize your investment.</p>
  </article>

  <article class="abs service-copy copy-audits">
    <h3>Performance Audits</h3>
    <p>Detailed on-site audits of the community and operator are offered, along with resident and staff satisfaction surveys. Additional services include analysis of the community's occupancy trends, financial performance, tour conversion rates and discounting strategies to provide you with a complete picture of the community's performance. These services can be provided on a quarterly or annual basis.</p>
  </article>

  <article class="abs service-copy copy-communications">
    <h3>Community Communications</h3>
    <p>Services include orchestrating the communication plan to announce the sale of the community to residents and staff, and working with the new operator to ensure that daily operations and key staff are maintained until the closing of the sale.</p>
  </article>

  <h2 class="abs contact-heading">Contact Us -</h2>
  <ul class="abs contact-details">
    <li>PHONE: 555.014.2271</li>
    <li>FAX: 555.014.3390</li>
    <li>INFO@BRANTORQUISSE.EXAMPLE</li>
  </ul>

  <div class="abs footer-bar"></div>
</main>
</body>
</html>
```